Corporate Travel Technology Company needs new Business Card design

We need a new business card design to reflect our re-branded company. Our company is called tolvEn (pronounced tolvenn) and we provide Business Intelligence and mobile travel management solutions for the corporate travel industry. Our multinational customers use our solutions to manage large travel budgets and frequent travellers, as well as to save money and reduce risk. We'd like to see designs that use the blue and green palette as well as our corporate logo (attached below). The design should communicate innovation, insight, forward thinking, contemporary, trusted.

Target Market(s)

Large multinational corporates and Travel Agencies.

Industry/Entity Type

Business

Contact Information for Business Card

Rosalind Mercer
Chief Executive
tolvEn
Phone number - +61 (0)2 8134 2907
Email address - rosalind.mercer@tolven-example.com
Mobile number - +61 (0)438 516 702
www.tolven-example.com

Font styles to use
Other font styles liked:
• Please use font as close to corporate logo as possible

Colors
0255a3
0393ce
00a990
33b8a4
33a6d7
3176b5

Requirements
Must have
• Please include the words;
• Mobile Travel Management
• Accelerating Travel Business Insights
• Use corporate logo - although icon can be stylised if needed

```html
<!DOCTYPE html>
<html lang="en">
<head>
<meta charset="utf-8">
<title>tolvEn Business Card</title>
<link rel="stylesheet" href="https://fonts.googleapis.com/css2?family=Open+Sans:wght@400;600;700&display=swap">
<style>
  :root {
    --backdrop: #3b3532;
    --card-black: #0c0c0d;
    --card-black-soft: #1a1b1d;
    --brand-cyan: #0aa9ea;
    --text-white: #f2f2f2;
    --logo-grey: #5f6f70;
  }
  * { margin: 0; padding: 0; box-sizing: border-box; }
  html, body {
    width: 1200px; height: 844px; overflow: hidden;
    background: var(--backdrop);
    font-family: "Open Sans", Arial, sans-serif;
  }
  .stage { position: relative; width: 1200px; height: 844px; }

  .card {
    position: absolute;
    top: 263px;
    width: 520px; height: 318px;
    background: radial-gradient(ellipse at 60% 40%, var(--card-black-soft), var(--card-black) 70%);
    overflow: hidden;
    box-shadow: 0 10px 30px rgba(0,0,0,0.5);
  }
  .card--front { left: 50px; }
  .card--back { left: 630px; }

  /* front */
  .band { position: absolute; left: 0; right: 0; height: 14px; background: var(--brand-cyan); }
  .band--top { top: 14px; }
  .band--bottom { bottom: 14px; }

  .mark-area {
    position: absolute; left: 0; top: 28px; bottom: 28px; width: 150px;
    background: linear-gradient(120deg, rgba(10,169,234,0.55), rgba(10,169,234,0.2));
  }

  .contact {
    position: absolute; left: 200px; top: 64px; width: 290px;
    color: var(--text-white);
  }
  .contact__name {
    font-size: 17px; font-weight: 700; color: var(--brand-cyan);
    letter-spacing: 0.2px; text-transform: uppercase;
    border-bottom: 1px solid var(--brand-cyan);
    padding-bottom: 2px; display: inline-block; padding-right: 8px;
  }
  .contact__title { font-size: 12px; margin: 3px 0 0 36px; }
  .contact__lines { list-style: none; margin: 34px 0 0 36px; font-size: 12.5px; line-height: 17px; }
  .contact__taglines { margin: 30px 0 0 24px; font-size: 13px; font-weight: 700; line-height: 18px; }

  /* back */
  .tab { position: absolute; width: 28px; height: 16px; background: var(--brand-cyan); }
  .tab--top { right: 0; top: 44px; }
  .tab--bottom { left: 0; bottom: 44px; }

  .logo {
    position: absolute; left: 50%; top: 50%;
    transform: translate(-50%, -50%);
    display: flex; align-items: center; gap: 14px;
  }
  .logo__dot { width: 30px; height: 30px; border-radius: 50%; background: var(--brand-cyan); }
  .logo__name { font-size: 62px; font-weight: 400; color: var(--logo-grey); letter-spacing: 1px; line-height: 1; }
</style>
</head>
<body>
<main class="stage">
  <section class="card card--front">
    <div class="band band--top"></div>
    <div class="mark-area" role="img" aria-label="Large brand mark decoration in cyan"></div>
    <div class="contact">
      <h1 class="contact__name">Rosalind Mercer</h1>
      <p class="contact__title">Chief Executive</p>
      <ul class="contact__lines">
        <li>+61 (0)2 8134 2907</li>
        <li>+61 (0)438 516 702</li>
        <li>rosalind.mercer@tolven-example.com</li>
        <li>www.tolven-example.com</li>
      </ul>
      <div class="contact__taglines">
        <p>Mobile Travel Management</p>
        <p>Accelerating Travel Business Insights</p>
      </div>
    </div>
    <div class="band band--bottom"></div>
  </section>

  <section class="card card--back">
    <div class="tab tab--top"></div>
    <div class="logo">
      <span class="logo__dot"></span>
      <span class="logo__name">tolvEn</span>
    </div>
    <div class="tab tab--bottom"></div>
  </section>
</main>
</body>
</html>
```